MRT Property - Business Cards

Looking for a business card & general letterhead, signage etc design for our new logo.

Colours:
000a20
0056a2
00b5ef
0088ce
68cef2

Fonts:
Poppins
Karla

Please keep look and feel of new brand - example in the zip package I sent.

```html
<!DOCTYPE html>
<html lang="en">
<head>
<meta charset="utf-8">
<title>MRT Property – Business Cards</title>
<link rel="stylesheet" href="https://fonts.googleapis.com/css2?family=Poppins:wght@500;600&family=Roboto:wght@400&display=swap">
<style>
  :root {
    --stage: #3a3b3e;
    --card: #10152b;
    --card-soft: #15203a;
    --brand-deep: #0056a2;
    --brand-mid: #0088ce;
    --brand-light: #68cef2;
    --text-light: #f2f4f8;
  }
  * { box-sizing: border-box; margin: 0; padding: 0; }
  html, body {
    width: 1200px; height: 900px; overflow: hidden;
    background: var(--stage);
  }
  .stage {
    width: 1200px; height: 900px;
    display: flex; flex-direction: column;
    align-items: center; justify-content: center; gap: 36px;
  }
  .card {
    position: relative;
    width: 700px; height: 400px;
    background: var(--card);
    border-radius: 26px;
    overflow: hidden;
    box-shadow: 0 10px 30px rgba(0,0,0,.45);
  }
  .wordmark {
    font-family: "Poppins", sans-serif;
    font-weight: 600;
    color: var(--brand-mid);
    display: flex; align-items: center; gap: 16px;
    white-space: nowrap;
  }
  .wordmark-dot {
    border-radius: 50%;
    background: var(--brand-light);
    flex: none;
  }
  /* front */
  .card-front { display: flex; align-items: center; justify-content: center; }
  .card-front .wordmark { font-size: 72px; }
  .card-front .wordmark-dot { width: 60px; height: 60px; }
  /* back */
  .back-sweep {
    position: absolute; left: -120px; top: 40px;
    width: 620px; height: 520px;
    border-radius: 50%;
    background: var(--card-soft);
  }
  .card-back .wordmark {
    position: absolute; right: 48px; top: 52px;
    font-size: 38px; gap: 10px;
  }
  .card-back .wordmark-dot { width: 32px; height: 32px; }
  .person {
    position: absolute; left: 60px; bottom: 88px;
    font-family: "Poppins", sans-serif;
  }
  .person-name {
    font-weight: 600; font-size: 24px; letter-spacing: .5px;
    color: var(--brand-mid); text-transform: uppercase;
  }
  .person-role {
    font-weight: 500; font-size: 19px; color: var(--brand-light);
  }
  .contact {
    position: absolute; left: 380px; top: 170px;
    font-family: "Roboto", sans-serif;
    color: var(--text-light); font-size: 19px; line-height: 1.3;
  }
  .contact-address { margin-bottom: 14px; }
  .contact-list { list-style: none; }
  .contact-list li { display: flex; align-items: center; gap: 10px; }
  .contact-list svg { width: 18px; height: 18px; flex: none; fill: var(--brand-mid); }
</style>
</head>
<body>
<main class="stage">
  <section class="card card-front">
    <div class="wordmark"><span class="wordmark-dot"></span>MRT Property</div>
  </section>

  <section class="card card-back">
    <div class="back-sweep"></div>
    <div class="wordmark"><span class="wordmark-dot"></span>MRT Property</div>

    <div class="person">
      <p class="person-name">Dorian Velasquez</p>
      <p class="person-role">Managing Director</p>
    </div>

    <div class="contact">
      <p class="contact-address">218 W Harbor Lane<br>Brookvale, CA 90012</p>
      <ul class="contact-list">
        <li>
          <svg viewBox="0 0 24 24" aria-hidden="true"><path d="M6.6 10.8a15.1 15.1 0 0 0 6.6 6.6l2.2-2.2a1 1 0 0 1 1-.25 11.4 11.4 0 0 0 3.6.57 1 1 0 0 1 1 1V20a1 1 0 0 1-1 1A17 17 0 0 1 3 4a1 1 0 0 1 1-1h3.5a1 1 0 0 1 1 1c0 1.25.2 2.45.57 3.57a1 1 0 0 1-.25 1z"/></svg>
          (555) 014-2290
        </li>
        <li>
          <svg viewBox="0 0 24 24" aria-hidden="true"><path d="M2 5h20v14H2z" opacity=".0"/><path d="M3 5h18a1 1 0 0 1 1 1v12a1 1 0 0 1-1 1H3a1 1 0 0 1-1-1V6a1 1 0 0 1 1-1zm1 2.3V8l8 5 8-5v-.7l-8 5z"/></svg>
          info@mrtproperty.com
        </li>
        <li>
          <svg viewBox="0 0 24 24" aria-hidden="true"><path d="M12 2a10 10 0 1 0 0 20 10 10 0 0 0 0-20zm-1 17.9A8 8 0 0 1 4.2 10.2L9 15v1a2 2 0 0 0 2 2zm6.9-2.5A2 2 0 0 0 16 16h-1v-3a1 1 0 0 0-1-1H8v-2h2a1 1 0 0 0 1-1V7h2a2 2 0 0 0 2-2v-.4a8 8 0 0 1 2.9 12.8z"/></svg>
          www.mrtproperty.com
        </li>
      </ul>
    </div>
  </section>
</main>
</body>
</html>
```